Brenlow Estates Website and Logo Design

We need a new logo and website designed for 'Brenlow Estates Ltd', which is a well established Guernsey property holding company founded in 1934.

The company does not currently have a website. The new website should be similar in style and layout to https://www.quorvanhall.example/.

Target Market(s)

Industry, Media, Tenants

Industry/Entity Type

Property Management

Logo Text

BEL OR Brenlow Estates Ltd OR BE

Coding

Coded - Design and coding required

Number of Pages Required

4 page

Font styles to use
Other font styles liked:
• Helvetica

Requirements
Must have
• The logo laying over the picture (like https://www.quorvanhall.example/).
• Big pictures on homepage (like https://www.quorvanhall.example/)

```html
<!DOCTYPE html>
<html lang="en">
<head>
<meta charset="utf-8">
<title>Brenlow Estates Limited</title>
<link href="https://fonts.googleapis.com/css2?family=Open+Sans:wght@400;600;700&display=swap" rel="stylesheet">
<style>
:root{
  --blue:#2a70b4;
  --ink:#333333;
  --body:#555555;
  --muted:#777777;
  --line:#dddddd;
  --grey:#f1f1f1;
  --white:#ffffff;
  --sea-top:#3f78c7;
  --sea-mid:#4f6f7a;
  --sea-low:#2f5563;
  --harbour-dark:#2c3a44;
}
*{box-sizing:border-box;margin:0;padding:0}
html,body{width:1200px;height:2586px;overflow:hidden;background:var(--white)}
body{font-family:"Open Sans",Arial,sans-serif;color:var(--ink);position:relative}
section,header,footer{position:absolute;left:0;width:1200px}
.abs{position:absolute}
.center{left:0;width:1200px;text-align:center}
.btn{position:absolute;background:var(--blue);color:var(--white);font-size:13px;font-weight:600;text-transform:uppercase;display:flex;align-items:center;justify-content:center;letter-spacing:.3px}

/* hero */
.hero{top:0;height:667px;background:linear-gradient(180deg,var(--sea-top) 0%,#6d93c9 14%,#8a8a80 24%,#6e6a5e 33%,var(--sea-mid) 42%,#3b6470 60%,var(--sea-low) 100%)}
.logo{left:76px;top:18px;width:250px;text-align:center;color:var(--white);font-size:30px;font-weight:600;line-height:40px}
.nav{top:38px;left:471px;height:41px;display:flex;align-items:center}
.nav a{color:var(--white);font-size:12.5px;font-weight:700;text-transform:uppercase;text-decoration:none;position:absolute;white-space:nowrap}
.nav .home{left:0;width:78px;height:41px;border:2px solid var(--white);display:flex;align-items:center;justify-content:center}
.hero-title{top:300px;font-size:48px;font-weight:700;color:var(--white);letter-spacing:1px}
.hero-sub{top:368px;font-size:27px;line-height:35px;color:var(--white);font-weight:600}
.arrow{position:absolute;top:347px;width:48px;height:48px;background:rgba(0,0,0,.45);display:flex;align-items:center;justify-content:center}

/* welcome */
.welcome{top:667px;height:309px}
.sec-title{font-size:24px;font-weight:700;text-transform:uppercase;color:var(--ink)}
.para{font-size:13px;line-height:26px;color:var(--body)}

/* why */
.why{top:976px;height:329px;background:linear-gradient(180deg,#3c4650 0%,var(--harbour-dark) 45%,#1f2f3a 100%)}
.why .sec-title{color:var(--white)}
.why .para{color:var(--white)}

/* cards */
.cards{top:1305px;height:460px}
.card{position:absolute;top:116px;width:330px;height:265px;border:1px solid var(--line);background:var(--white);text-align:center}
.card .icon{position:absolute;left:116px;top:-49px;width:98px;height:98px;border-radius:50%;background:#f2f2f2;border:5px solid var(--white);box-shadow:0 0 0 1px var(--line);display:flex;align-items:center;justify-content:center}
.card h3{position:absolute;top:73px;width:100%;font-size:18px;font-weight:700;text-transform:uppercase}
.card p{position:absolute;top:109px;left:30px;right:30px;font-size:13px;line-height:26px;color:var(--body)}
.card .btn{left:75px;top:239px;width:180px;height:47px}

/* posts */
.posts{top:1765px;height:393px;background:var(--grey)}
.col-title{position:absolute;top:38px;font-size:24px;font-weight:700;text-transform:uppercase}
.post{position:absolute;width:500px;height:100px}
.thumb{position:absolute;left:0;top:0;width:150px;height:100px}
.post h4{position:absolute;left:179px;top:4px;font-size:14px;font-weight:700;color:var(--blue);text-transform:uppercase}
.post p{position:absolute;left:179px;top:28px;width:330px;font-size:13px;line-height:26px;color:var(--body)}
.post .date{font-weight:700;color:var(--ink)}

/* newsletter */
.news{top:2158px;height:247px}
.email{position:absolute;left:343px;top:149px;width:324px;height:46px;border:1px solid var(--line);font-size:13px;color:#999;padding-left:14px;display:flex;align-items:center}

/* footer */
.footer{top:2405px;height:181px;background:var(--grey)}
.social{position:absolute;top:100px;width:22px;height:22px;border-radius:4px;background:#9a9a9a}
</style>
</head>
<body>

<header class="hero" role="img" aria-label="Photograph of a Guernsey harbour town with boats moored on calm water">
  <div class="abs logo">Brenlow Estates<br>Limited</div>
  <nav class="abs nav">
    <a class="home" href="#">Home</a>
    <a href="#" style="left:101px">About Us</a>
    <a href="#" style="left:213px">Services</a>
    <a href="#" style="left:319px">Blog</a>
    <a href="#" style="left:399px">Careers</a>
    <a href="#" style="left:501px">Contact</a>
    <svg class="abs" style="left:643px;top:13px" width="14" height="14" viewBox="0 0 14 14"><circle cx="5.5" cy="5.5" r="4" fill="none" stroke="#fff" stroke-width="2"/><line x1="8.5" y1="8.5" x2="13" y2="13" stroke="#fff" stroke-width="2"/></svg>
  </nav>
  <h1 class="abs center hero-title">BRENLOW ESTATES LIMITED</h1>
  <p class="abs center hero-sub">Brenlow Estates Limited is a family-owned Guernsey<br>property holding company.</p>
  <div class="arrow" style="left:0"><svg width="12" height="20" viewBox="0 0 12 20"><polyline points="10,2 2,10 10,18" fill="none" stroke="#fff" stroke-width="2"/></svg></div>
  <div class="arrow" style="right:0"><svg width="12" height="20" viewBox="0 0 12 20"><polyline points="2,2 10,10 2,18" fill="none" stroke="#fff" stroke-width="2"/></svg></div>
</header>

<section class="welcome">
  <h2 class="abs center sec-title" style="top:47px">Welcome to Brenlow Estates Limited</h2>
  <p class="abs para" style="left:80px;width:1040px;top:99px;text-align:center">Brenlow Estates Limited (BEL) is a family-owned Guernsey property holding company. It purchases properties that are considered to have potential for development either through refurbishment or by obtaining planning permission to change its classification from, for example, industrial premises to offices or retail outlets, or by the marriage value of buying an adjacent property to one already owned by BEL.</p>
  <a class="btn" style="left:510px;top:214px;width:180px;height:48px">Read More</a>
</section>

<section class="why" role="img" aria-label="Darkened photograph of a Guernsey harbour with moored boats and buoys">
  <h2 class="abs center sec-title" style="top:45px">Why Guernsey?</h2>
  <p class="abs para" style="left:80px;width:1040px;top:106px;text-align:center">The Bailiwick of Guernsey is a British Crown dependency in the English Channel. The benefit of establishing a company in Guernsey is the island's low tax jurisdiction since there are no capital taxes and no corporation taxes for many companies. Consequently since the 1980s the island's development as an ideal financial centre for the establishment of institutions and banks has thrived.</p>
  <a class="btn" style="left:510px;top:220px;width:180px;height:48px">Read More</a>
</section>

<section class="cards">
  <div class="card" style="left:76px">
    <div class="icon"><svg width="32" height="32" viewBox="0 0 32 32"><rect x="3" y="6" width="26" height="23" rx="2" fill="none" stroke="#666" stroke-width="2"/><line x1="3" y1="12" x2="29" y2="12" stroke="#666" stroke-width="2"/><line x1="10" y1="2" x2="10" y2="8" stroke="#666" stroke-width="2"/><line x1="22" y1="2" x2="22" y2="8" stroke="#666" stroke-width="2"/><path d="M7 16h4v3H7zM14 16h4v3h-4zM21 16h4v3h-4zM7 22h4v3H7zM14 22h4v3h-4zM21 22h4v3h-4z" fill="#666"/></svg></div>
    <h3>Yesterday</h3>
    <p>BEL was founded in 1934 by Henry Brenlow to manage both his own extensive investments and his property portfolio in Guernsey.</p>
    <a class="btn">Read More</a>
  </div>
  <div class="card" style="left:435px">
    <div class="icon"><svg width="32" height="32" viewBox="0 0 32 32"><rect x="3" y="6" width="26" height="23" rx="2" fill="none" stroke="#666" stroke-width="2"/><line x1="3" y1="12" x2="29" y2="12" stroke="#666" stroke-width="2"/><line x1="10" y1="2" x2="10" y2="8" stroke="#666" stroke-width="2"/><line x1="22" y1="2" x2="22" y2="8" stroke="#666" stroke-width="2"/><path d="M7 16h4v3H7zM14 16h4v3h-4zM21 16h4v3h-4zM7 22h4v3H7zM14 22h4v3h-4zM21 22h4v3h-4z" fill="#666"/></svg></div>
    <h3>Today</h3>
    <p>The Brenlow family has steadily built on the foundations set out by the founder and each generation develops and manages the company appropriate to the era.</p>
    <a class="btn">Read More</a>
  </div>
  <div class="card" style="left:795px">
    <div class="icon"><svg width="32" height="32" viewBox="0 0 32 32"><rect x="3" y="6" width="26" height="23" rx="2" fill="none" stroke="#666" stroke-width="2"/><line x1="3" y1="12" x2="29" y2="12" stroke="#666" stroke-width="2"/><line x1="10" y1="2" x2="10" y2="8" stroke="#666" stroke-width="2"/><line x1="22" y1="2" x2="22" y2="8" stroke="#666" stroke-width="2"/><path d="M7 16h4v3H7zM14 16h4v3h-4zM21 16h4v3h-4zM7 22h4v3H7zM14 22h4v3h-4zM21 22h4v3h-4z" fill="#666"/></svg></div>
    <h3>Tomorrow</h3>
    <p>In keeping with its past project development philosophy, its intrinsic understanding of the local property market and the successful management..</p>
    <a class="btn">Read More</a>
  </div>
</section>

<section class="posts">
  <h2 class="col-title" style="left:76px">Blog Posts</h2>
  <h2 class="col-title" style="left:614px">News &amp; Event</h2>

  <article class="post" style="left:76px;top:102px">
    <div class="thumb" role="img" aria-label="Photograph of a harbour town waterfront" style="background:linear-gradient(180deg,#7fa3d6 0%,#9a9686 45%,#55707c 100%)"></div>
    <h4>Consectetuer adipiscing elit</h4>
    <p>Duis aliquam nibh a dui iaculis viverra id a velit. Vivamus egestas risus in magna varius commodo vel ornare neque..</p>
  </article>
  <article class="post" style="left:76px;top:243px">
    <div class="thumb" role="img" aria-label="Photograph of boats in a bay under blue sky" style="background:linear-gradient(180deg,#4f86d0 0%,#8fb0de 45%,#2f5f8c 100%)"></div>
    <h4>Consectetuer adipiscing elit</h4>
    <p>Duis aliquam nibh a dui iaculis viverra id a velit. Vivamus egestas risus in magna varius commodo vel ornare neque..</p>
  </article>
  <article class="post" style="left:614px;top:102px">
    <div class="thumb" role="img" aria-label="Photograph of a fishing boat moored at a quay" style="background:linear-gradient(180deg,#4e7d8c 0%,#3e6a78 55%,#23424e 100%)"></div>
    <h4>Consectetuer adipiscing elit</h4>
    <p>Duis aliquam nibh a dui iaculis viverra id a velit. Vivamus egestas risus in magna varius commodo vel ornare neque..</p>
  </article>
  <article class="post" style="left:614px;top:243px">
    <div class="thumb" role="img" aria-label="Aerial photograph of a marina full of yachts" style="background:linear-gradient(135deg,#a89a7a 0%,#6f7e74 50%,#3e5a5a 100%)"></div>
    <h4>Consectetuer adipiscing elit</h4>
    <p>Duis aliquam nibh a dui iaculis viverra id a velit. Vivamus egestas risus in magna varius<br><span class="date">Dec 02, 2016</span></p>
  </article>
</section>

<section class="news">
  <h2 class="abs center sec-title" style="top:48px">Subscribe Newsletter</h2>
  <p class="abs center para" style="top:96px">Vestibulum ante ipsum primis in faucibus orci luctus et ultrices posuere cubilia..</p>
  <div class="email">Enter Email Address</div>
  <a class="btn" style="left:678px;top:149px;width:179px;height:46px;gap:10px">
    <svg width="14" height="11" viewBox="0 0 14 11"><rect x="0" y="0" width="14" height="11" fill="#fff"/><polyline points="0,0 7,6 14,0" fill="none" stroke="#2a70b4" stroke-width="1.5"/></svg>Sign Up</a>
</section>

<footer class="footer">
  <p class="abs center" style="top:57px;font-size:12.5px;color:var(--muted)">Copyright © 2016. Company Name. All Right Reserved</p>
  <span class="social" style="left:517px"></span>
  <span class="social" style="left:553px"></span>
  <span class="social" style="left:589px"></span>
  <span class="social" style="left:625px"></span>
  <span class="social" style="left:661px"></span>
</footer>

</body>
</html>
```